Kelvor Engineers: Why you should hire us keepsake

New design. Open to plastic cards. We are an engineering firm that designs cell phone towers and commercial buildings. Please check out our website www.kelvorstruct.com for more details. We want people to remember our card and for it to be useful if possible. We want the same look and feel on these cards to be translated to other marketing material we may need such as brochures.

Target Market(s)

Architects, Developers and Telecommunication Carriers

Industry/Entity Type

Engineering

Contact Information for Business Card

Card with our company colors, logo, and innovative design with elements related to our industry.

Font styles to use
Sans Serif

Colors
9bcb3c
abd036
0255a3

Requirements
Must have
• Sleek and hip design
Nice to have
• Bright lime green and navy coloring that pops with an innovative design.
Should not have
• A basic and boring design

```html
<!DOCTYPE html>
<html lang="en">
<head>
<meta charset="utf-8">
<title>Kelvor Engineers – Business Card</title>
<link rel="stylesheet" href="https://fonts.googleapis.com/css2?family=Roboto:wght@400;500;900&family=Roboto+Condensed:wght@700&display=swap">
<style>
  :root {
    --backdrop: #2b2b2b;
    --navy: #022b5c;
    --lime: #1dff1d;
    --paper: #f1f1f1;
    --ink: #4a4a4a;
    --white: #ffffff;
    --rule: #c9c9c9;
  }
  * { margin: 0; padding: 0; box-sizing: border-box; }
  html, body { width: 1200px; height: 960px; overflow: hidden; }
  body {
    background: var(--backdrop);
    position: relative;
    font-family: "Roboto", Arial, sans-serif;
  }
  .card {
    position: absolute;
    width: 600px;
    height: 342px;
    border-radius: 22px;
    overflow: hidden;
  }
  .card-front {
    left: 322px; top: 108px;
    background: var(--navy);
    color: var(--white);
  }
  .front-name {
    position: absolute;
    left: 0; right: 0; top: 108px;
    text-align: center;
    font-weight: 900;
    font-size: 104px;
    line-height: 1;
    letter-spacing: -2px;
    color: var(--lime);
  }
  .front-tagline {
    position: absolute;
    left: 0; right: 0; top: 265px;
    display: flex; justify-content: center; align-items: center; gap: 4px;
    font-weight: 500;
    font-size: 15px;
    letter-spacing: 0.2px;
  }
  .front-tagline .dash { width: 30px; height: 1.5px; background: var(--white); }
  .front-cities {
    position: absolute;
    left: 0; right: 0; top: 286px;
    text-align: center;
    font-size: 15px;
    letter-spacing: 0.8px;
  }
  .card-back {
    left: 320px; top: 493px;
    background: var(--paper);
  }
  .back-corners { position: absolute; inset: 0; }
  .back-name {
    position: absolute;
    left: 40px; top: 134px;
    width: 250px;
    text-align: center;
    font-weight: 900;
    font-size: 62px;
    line-height: 1;
    letter-spacing: -1px;
    color: var(--lime);
  }
  .divider {
    position: absolute;
    left: 303px; top: 108px;
    width: 1px; height: 126px;
    background: var(--rule);
  }
  .person {
    position: absolute;
    left: 332px; top: 114px;
    font-family: "Roboto Condensed", Arial, sans-serif;
    font-weight: 700;
    font-size: 21px;
    color: var(--lime);
  }
  .contacts {
    position: absolute;
    left: 332px; top: 148px;
    list-style: none;
  }
  .contacts li {
    display: flex; align-items: center; gap: 10px;
    height: 19.5px;
    font-size: 14.5px;
    color: var(--ink);
  }
  .contacts svg { width: 12px; height: 12px; fill: var(--lime); flex: none; }
</style>
</head>
<body>

<section class="card card-front">
  <div class="front-name">Kelvor</div>
  <div class="front-tagline"><span class="dash"></span>STRUCTURAL &amp; TOWER ENGINEERING<span class="dash"></span></div>
  <div class="front-cities">Ashford | Millbrook | Dunmore | Fairhaven</div>
</section>

<section class="card card-back">
  <svg class="back-corners" viewBox="0 0 600 342" aria-hidden="true">
    <path d="M0,0 H150 Q60,4 0,80 Z" fill="var(--navy)"/>
    <path d="M0,0 H88 Q30,32 0,80 Z" fill="var(--lime)"/>
    <path d="M600,342 H478 Q568,322 600,262 Z" fill="var(--navy)"/>
    <path d="M600,342 H514 Q578,312 600,262 Z" fill="var(--lime)"/>
  </svg>
  <div class="back-name">Kelvor</div>
  <div class="divider"></div>
  <div class="person">DANA HOLLOWAY REESE</div>
  <ul class="contacts">
    <li><svg viewBox="0 0 12 12"><path d="M2.5 0.5 L4.5 3 L3.4 4.4 Q4.5 6.8 7.6 8.6 L9 7.5 L11.5 9.5 L10 11.5 Q5 11 0.8 4.5 Q0.5 2 2.5 0.5 Z"/></svg>555.014.2210</li>
    <li><svg viewBox="0 0 12 12"><path d="M3 0 H9 Q10 0 10 1 V11 Q10 12 9 12 H3 Q2 12 2 11 V1 Q2 0 3 0 Z M3.4 1.5 V9.5 H8.6 V1.5 Z"/></svg>555.019.4478</li>
    <li><svg viewBox="0 0 12 12"><path d="M0.5 2.5 H11.5 L6 6.5 Z M0.5 3.8 L6 7.8 L11.5 3.8 V10 H0.5 Z"/></svg>dreese@kelvorstruct.com</li>
    <li><svg viewBox="0 0 12 12"><circle cx="6" cy="6" r="5.5"/><path d="M3 3 Q5 4 4.5 6 Q6 7 5.5 9.5 M8 2.5 Q7 4.5 9 5.5" stroke="var(--paper)" stroke-width="1.1" fill="none"/></svg>www.kelvorstruct.com</li>
  </ul>
</section>

</body>
</html>
```